Amber Fox Quest "Your path, my quest"

Individual coaching: life coach & projec Amberfox (amber fox) represents the flight, freedom to be happy. The mission: to be well in his mission in life. sober and soft design which refers professionalism, safety, wellness, balance, personal development. my coordinates = Marta Kovin Life & Project 0462 coach / 31.78.25 marta@amberfoxquest.be

Reason: Business card that refers to the professional (life coaching) and sweetness / freedom of achievement.

Target Market(s)

adults in search of well being, balance for themselves and / or their children

Contact Information for Business Card

Marta Kovin
Life & project coach
0462/31.78.25
marta@amberfoxquest.be

Requirements
Must have
• AMBER FOX QUEST logo tag "Your flight, my mission"
Nice to have
• originality pure appearance, gentle and professional
Should not have
• overdoing banking organization

```html
<!DOCTYPE html>
<html lang="fr">
<head>
<meta charset="utf-8">
<title>Amber Fox Quest – Business Card</title>
<link rel="stylesheet" href="https://fonts.googleapis.com/css2?family=Roboto:wght@400;500&family=Fredoka:wght@600&family=Saira+Semi+Condensed:wght@600&display=swap">
<style>
  :root {
    --backdrop: #cbcbcb;
    --navy: #114277;
    --sky: #2a80c1;
    --charcoal: #4a4848;
    --paper: #fafafa;
    --ink: #4d4d4d;
    --white: #ffffff;
  }
  * { margin: 0; padding: 0; box-sizing: border-box; }
  html, body {
    width: 1200px;
    height: 1005px;
    overflow: hidden;
    background: var(--backdrop);
  }
  .stage {
    position: relative;
    width: 1200px;
    height: 1005px;
  }
  .card {
    position: absolute;
    left: 300px;
    width: 600px;
    height: 340px;
    overflow: hidden;
  }
  .card--front {
    top: 140px;
    background: var(--navy);
    display: flex;
    align-items: center;
    justify-content: center;
  }
  .card--back {
    top: 525px;
    background: var(--paper);
  }
  .brand {
    font-family: "Fredoka", sans-serif;
    font-weight: 600;
    line-height: 1;
    text-align: center;
  }
  .brand--front {
    color: var(--white);
    font-size: 46px;
  }
  .brand--back {
    position: absolute;
    top: 62px;
    right: 40px;
    color: var(--navy);
    font-size: 36px;
  }
  .brand__line { display: block; }
  .brand__line--sub {
    font-size: 0.62em;
    letter-spacing: 0.45em;
    margin-top: 8px;
    padding-left: 0.45em;
  }
  .waves {
    position: absolute;
    inset: 0;
    width: 600px;
    height: 340px;
  }
  .person {
    position: absolute;
    left: 44px;
    top: 118px;
  }
  .person__name {
    font-family: "Saira Semi Condensed", sans-serif;
    font-weight: 600;
    font-size: 27px;
    color: var(--navy);
    line-height: 1;
  }
  .person__role {
    font-family: "Roboto", sans-serif;
    font-size: 13px;
    color: var(--ink);
    margin-top: 6px;
  }
  .contacts {
    position: absolute;
    left: 60px;
    top: 200px;
    list-style: none;
    font-family: "Roboto", sans-serif;
    font-size: 13px;
    color: var(--ink);
  }
  .contacts__item {
    display: flex;
    align-items: center;
    gap: 10px;
    height: 21px;
  }
  .contacts__icon { width: 14px; height: 14px; fill: var(--navy); }
  .tagline {
    position: absolute;
    right: 44px;
    top: 205px;
    font-family: "Roboto", sans-serif;
    font-size: 15px;
    line-height: 1.35;
    color: var(--white);
    text-align: center;
  }
</style>
</head>
<body>
<main class="stage">
  <section class="card card--front" aria-label="Recto de la carte">
    <h1 class="brand brand--front">
      <span class="brand__line">Amber Fox</span>
      <span class="brand__line brand__line--sub">QUEST</span>
    </h1>
  </section>

  <section class="card card--back" aria-label="Verso de la carte">
    <svg class="waves" viewBox="0 0 600 340" aria-hidden="true">
      <path d="M600,128 C480,150 420,262 330,292 C240,322 120,316 0,310 L0,340 L600,340 Z" fill="var(--charcoal)"/>
      <path d="M600,112 C470,136 410,248 320,278 C230,308 110,302 0,296" fill="none" stroke="var(--sky)" stroke-width="8"/>
      <path d="M290,262 C220,292 150,296 80,298 C170,290 230,280 290,262 Z" fill="none" stroke="var(--sky)" stroke-width="5"/>
    </svg>

    <div class="brand brand--back">
      <span class="brand__line">Amber Fox</span>
      <span class="brand__line brand__line--sub">QUEST</span>
    </div>

    <div class="person">
      <h2 class="person__name">Marta Kovin</h2>
      <p class="person__role">Life &amp; project coach</p>
    </div>

    <ul class="contacts">
      <li class="contacts__item">
        <svg class="contacts__icon" viewBox="0 0 24 24"><path d="M3 9c0-3 4-5 9-5s9 2 9 5v2h-5V9H8v2H3z M6 12h12l2 8H4z"/></svg>
        <span>0462/31.78.25</span>
      </li>
      <li class="contacts__item">
        <svg class="contacts__icon" viewBox="0 0 24 24"><path d="M2 5h20v14H2z M3 6l9 7 9-7" fill="var(--navy)" stroke="var(--white)" stroke-width="1.5"/></svg>
        <span>marta@amberfoxquest.be</span>
      </li>
      <li class="contacts__item">
        <svg class="contacts__icon" viewBox="0 0 24 24"><circle cx="12" cy="12" r="10"/><path d="M2 12h20M12 2v20M5 6h14M5 18h14" stroke="var(--white)" stroke-width="1.3" fill="none"/></svg>
        <span>www.amberfoxquest.be</span>
      </li>
    </ul>

    <p class="tagline">Votre chemin,<br>ma quête</p>
  </section>
</main>
</body>
</html>
```